Business Card Design for Varomir Facility Services

We are looking for a Business Card Design for the Company "Varomir Facility Services."
Front side:
- Company Logo (small)
- Company Name, address, pohone, website and personal data.
- white background, for text e.g. company colors (blue or green like in the logo)
Please use following data:
Company data:
Varomir Facility Services Kostelac
Birkenhaldweg 14
6330 Cham
www.varomir-fs.ch
Person data:
Tarik Kostelac
Geschäftsführer
+41 76 519 47 83
info@varomir-fs.ch
Back side:
could be colored in blue or green
please use a big logo sing and some smaller icons to say what is all beeing offered in facility services, like cleaning, maintenance cleaning
industrial cleaning, caretaking, gardening, disposal. There is no need for everyone of the icons if there are similar or an icon is standing for more of them.
colors to use:
blue: HEX 246BB0
green: HEX 52B33E

```html
<!DOCTYPE html>
<html lang="de">
<head>
<meta charset="utf-8">
<title>Varomir Facility Services – Visitenkarte</title>
<link href="https://fonts.googleapis.com/css2?family=Source+Sans+3:wght@400;600&display=swap" rel="stylesheet">
<style>
  :root {
    --blue: #1668b3;
    --green: #56b847;
    --ink: #1c2229;
    --text: #3a3f45;
    --paper: #ffffff;
  }
  * { margin: 0; padding: 0; box-sizing: border-box; }
  html, body { width: 1200px; height: 960px; overflow: hidden; background: var(--paper); }
  body { position: relative; font-family: "Source Sans 3", "Source Sans Pro", sans-serif; }

  .card {
    position: absolute; left: 286px; width: 629px; height: 360px;
    background: var(--paper); overflow: hidden;
    box-shadow: 0 2px 6px rgba(0,0,0,.35);
  }
  .card--front { top: 109px; }
  .card--back { top: 492px; }

  /* front */
  .front-edge { position: absolute; left: 0; top: 0; width: 22px; height: 360px; }
  .front-panel { position: absolute; left: 246px; top: 0; width: 383px; height: 360px; background: var(--blue); }
  .front-brand {
    position: absolute; left: 0; right: 0; top: 160px; text-align: center;
    color: var(--paper); font-weight: 600; font-size: 26px; letter-spacing: .5px;
  }
  .person { position: absolute; left: 51px; top: 62px; }
  .person__name { font-weight: 600; font-size: 24px; color: var(--ink); line-height: 30px; }
  .person__role { font-size: 18px; color: var(--ink); line-height: 24px; }
  .address { position: absolute; left: 52px; top: 150px; font-size: 16px; color: var(--ink); line-height: 26.5px; }
  .contacts { position: absolute; left: 52px; top: 218px; list-style: none; }
  .contacts li { display: flex; align-items: center; height: 26.5px; font-size: 16.5px; color: var(--ink); }
  .contacts svg { width: 16px; height: 16px; margin-right: 15px; flex: none; }

  /* back */
  .back-brand {
    position: absolute; left: 0; right: 0; top: 178px; text-align: center;
    color: var(--blue); font-weight: 600; font-size: 34px; letter-spacing: .5px;
  }
  .services { position: absolute; top: 266px; left: 0; width: 629px; height: 60px; }
  .services ul { position: absolute; top: 0; list-style: none; }
  .services li { display: flex; align-items: center; height: 26.5px; font-size: 17.5px; color: var(--text); }
  .services svg { width: 16px; height: 16px; margin-right: 8px; flex: none; }
  .services .col-1 { left: 39px; }
  .services .col-2 { left: 273px; }
  .services .col-3 { left: 484px; }
  .back-band { position: absolute; left: 0; bottom: 0; width: 629px; height: 23px; }
</style>
</head>
<body>
<svg width="0" height="0" style="position:absolute">
  <defs>
    <symbol id="sparkle" viewBox="0 0 16 16">
      <path d="M8 0 L9.4 6.6 L16 8 L9.4 9.4 L8 16 L6.6 9.4 L0 8 L6.6 6.6 Z" fill="#1668b3" transform="rotate(-12 8 8)"/>
    </symbol>
  </defs>
</svg>

<section class="card card--front" aria-label="Vorderseite">
  <svg class="front-edge" viewBox="0 0 22 360" preserveAspectRatio="none">
    <rect width="22" height="360" fill="#1668b3"/>
    <polygon points="0,73 22,60 22,115 0,128" fill="#56b847"/>
    <polygon points="0,73 22,60 22,63 0,76" fill="#fff"/>
    <polygon points="0,125 22,112 22,115 0,128" fill="#fff"/>
  </svg>

  <div class="person">
    <p class="person__name">Tarik Kostelac</p>
    <p class="person__role">Geschäftsführer</p>
  </div>
  <p class="address">Birkenhaldweg 14<br>6330 Cham</p>
  <ul class="contacts">
    <li>
      <svg viewBox="0 0 16 16"><path d="M3.2 1 L5.6 3.6 L4.4 5.6 Q6 9 10.4 11.6 L12.4 10.4 L15 12.8 L13 15 Q7 15 3.5 10.5 Q1 7.5 1 3 Z" fill="#1668b3"/></svg>
      +41 76 519 47 83
    </li>
    <li>
      <svg viewBox="0 0 16 16"><rect x="0.5" y="3" width="15" height="10" fill="#1668b3"/><path d="M1 3.5 L8 9 L15 3.5 M1 12.5 L6 7.5 M15 12.5 L10 7.5" stroke="#fff" stroke-width="1.1" fill="none"/></svg>
      info@varomir-fs.ch
    </li>
    <li>
      <svg viewBox="0 0 16 16"><circle cx="8" cy="8" r="7.3" fill="#1668b3"/><path d="M1 8 H15 M8 1 V15 M3 3.5 Q8 6 13 3.5 M3 12.5 Q8 10 13 12.5" stroke="#fff" stroke-width="1" fill="none"/></svg>
      www.varomir-fs.ch
    </li>
  </ul>

  <div class="front-panel">
    <p class="front-brand">Varomir Facility Services</p>
  </div>
</section>

<section class="card card--back" aria-label="Rückseite">
  <p class="back-brand">Varomir Facility Services</p>

  <div class="services">
    <ul class="col-1">
      <li><svg><use href="#sparkle"/></svg>Like cleaning</li>
      <li><svg><use href="#sparkle"/></svg>Maintenance cleaning</li>
    </ul>
    <ul class="col-2">
      <li><svg><use href="#sparkle"/></svg>Industrial cleaning</li>
      <li><svg><use href="#sparkle"/></svg>Caretaking</li>
    </ul>
    <ul class="col-3">
      <li><svg><use href="#sparkle"/></svg>Gardening</li>
      <li><svg><use href="#sparkle"/></svg>Disposal</li>
    </ul>
  </div>

  <svg class="back-band" viewBox="0 0 629 23" preserveAspectRatio="none">
    <rect width="629" height="23" fill="#1668b3"/>
    <polygon points="44,0 585,0 573,23 56,23" fill="#fff"/>
    <polygon points="48,0 581,0 569,23 60,23" fill="#56b847"/>
  </svg>
</section>
</body>
</html>
```